Red Mo's Wine Label Project

We need a new entry level wine label called "Red Mo's" for a range of wines we are developing from inland Australia. Our company is made up of three youngish guys who live hard and love taking the mickey. Red Mo is Red Morrie - the largest and loudest of the three partners (and ideally this label will take the mickey out of him). We've grown the grapes ourselves for this first release which will be a 2012 Pinot Gris. Wine style is dry, young, fresh and contemporary and pitched at the sub AUD $10 retail price point. The package will be flint (clear) claret shape bottle with plain screwcap (colour matched to suit the winning label design).

I've attached a couple of photos of Red Morrie to give you some idea of his presence and persona.

Target Market(s)

Semi educated 25 - 40 year old wine drinkers. Skewed towards females.

Industry/Entity Type

Retail

Requirements
Should not have
• Anything traditional or old fashioned

```html
<!DOCTYPE html>
<html lang="en">
<head>
<meta charset="utf-8">
<title>Red Mo's Pinot Gris – Colour Scheme 4</title>
<link href="https://fonts.googleapis.com/css2?family=Comfortaa:wght@700&family=Roboto:wght@400;500&family=Tinos&display=swap" rel="stylesheet">
<style>
  :root {
    --sidebar-grey: #6d6a69;
    --bar-grey: #6f6d6c;
    --faint-grey: #ebebeb;
    --label-black: #0b0b0b;
    --wine-purple: #8c2250;
    --cap-purple: #a4275e;
    --accent-yellow: #f2d21b;
    --text-grey: #555555;
    --white: #ffffff;
  }
  * { margin: 0; padding: 0; box-sizing: border-box; }
  html, body { width: 1200px; height: 900px; overflow: hidden; background: var(--white); }
  .board { position: relative; width: 1200px; height: 900px; overflow: hidden; background: var(--white); font-family: 'Roboto', Arial, sans-serif; }

  .sidebar { position: absolute; left: 0; top: 0; width: 85px; height: 900px; background: var(--sidebar-grey); }

  .backdrop-band { position: absolute; background: var(--faint-grey); }
  .band-left { left: 85px; top: 296px; width: 880px; height: 36px; }
  .band-right { left: 950px; top: 398px; width: 250px; height: 34px; }
  .backdrop-name { position: absolute; left: 575px; top: 560px; font-family: 'Comfortaa', sans-serif; font-weight: 700; font-size: 120px; color: var(--faint-grey); white-space: nowrap; line-height: 1; }

  .label { position: absolute; left: 225px; top: 23px; width: 332px; height: 848px; background: var(--label-black); overflow: hidden; }
  .label-mark { position: absolute; left: 0; top: 250px; width: 100%; display: flex; justify-content: center; align-items: center; gap: 10px; font-family: 'Comfortaa', sans-serif; font-weight: 700; font-size: 46px; color: var(--white); line-height: 1; white-space: nowrap; }
  .label-mark .dot { width: 22px; height: 22px; border-radius: 50%; background: var(--wine-purple); flex: none; }
  .label-wordmark { position: absolute; left: 103px; top: 396px; font-family: 'Comfortaa', sans-serif; font-weight: 700; font-size: 26px; color: var(--white); line-height: 1; white-space: nowrap; }
  .label-variety { position: absolute; left: 103px; top: 428px; font-family: 'Comfortaa', sans-serif; font-weight: 700; font-size: 13px; color: var(--white); letter-spacing: 0.5px; white-space: nowrap; }
  .label-variety .vintage { color: var(--wine-purple); }
  .label-pattern { position: absolute; left: 12px; top: 690px; font-family: 'Comfortaa', sans-serif; font-weight: 700; font-size: 70px; color: var(--wine-purple); white-space: nowrap; line-height: 1; }
  .label-volume { position: absolute; left: 14px; bottom: 12px; font-family: 'Tinos', 'Times New Roman', serif; font-size: 17px; color: var(--white); line-height: 1.1; }

  .section-bar { position: absolute; background: var(--bar-grey); color: var(--white); font-size: 18px; text-transform: uppercase; display: flex; align-items: center; padding-left: 18px; white-space: nowrap; }
  .scheme-bar { left: 738px; top: 72px; width: 462px; height: 34px; }
  .scheme-bar strong { font-weight: 500; margin-right: 5px; }
  .scheme-bar .scheme-number { color: var(--accent-yellow); margin-left: 5px; }
  .pms-bar { left: 1020px; top: 764px; width: 180px; height: 28px; font-size: 16px; padding-left: 26px; }

  .bottle { position: absolute; left: 790px; top: 130px; width: 170px; height: 765px; }
  .bottle-label { position: absolute; left: 810px; top: 407px; width: 125px; height: 320px; background: var(--label-black); overflow: hidden; }
  .bottle-label .mini-mark { position: absolute; left: 0; top: 80px; width: 100%; display: flex; justify-content: center; align-items: center; gap: 4px; font-family: 'Comfortaa', sans-serif; font-weight: 700; font-size: 16px; color: var(--white); white-space: nowrap; }
  .bottle-label .mini-mark .dot { width: 8px; height: 8px; border-radius: 50%; background: var(--wine-purple); flex: none; }
  .bottle-label .mini-wordmark { position: absolute; left: 38px; top: 146px; font-family: 'Comfortaa', sans-serif; font-weight: 700; font-size: 10px; color: var(--white); white-space: nowrap; }
  .bottle-label .mini-variety { position: absolute; left: 38px; top: 159px; font-family: 'Comfortaa', sans-serif; font-weight: 700; font-size: 6px; color: var(--white); white-space: nowrap; }
  .bottle-label .mini-variety span { color: var(--wine-purple); }
  .bottle-label .mini-pattern { position: absolute; left: 8px; top: 245px; font-family: 'Comfortaa', sans-serif; font-weight: 700; font-size: 24px; color: var(--wine-purple); white-space: nowrap; }
  .bottle-label .mini-volume { position: absolute; left: 5px; bottom: 4px; font-family: 'Tinos', serif; font-size: 7px; color: var(--white); line-height: 1.1; }

  .swatches { position: absolute; left: 1020px; top: 800px; list-style: none; }
  .swatches li { display: flex; align-items: center; gap: 6px; height: 22px; margin-bottom: 10px; font-size: 13px; color: var(--text-grey); white-space: nowrap; }
  .swatches .chip { width: 20px; height: 20px; border-radius: 4px; }
  .chip-purple { background: var(--wine-purple); }
  .chip-black { background: var(--label-black); }
</style>
</head>
<body>
<main class="board">
  <div class="sidebar"></div>

  <div class="backdrop-band band-left"></div>
  <div class="backdrop-band band-right"></div>
  <div class="backdrop-name" aria-hidden="true">Red Mo's</div>

  <section class="label" aria-label="Flat wine label artwork">
    <div class="label-mark"><span class="dot"></span>Red Mo's</div>
    <div class="label-wordmark">RED Mo's</div>
    <div class="label-variety">PIGNOT GRIS <span class="vintage">2012</span></div>
    <div class="label-pattern" aria-hidden="true">Red Mo's</div>
    <div class="label-volume">12% Vol.<br>750ml</div>
  </section>

  <div class="section-bar scheme-bar"><strong>Colour</strong> Scheme <span class="scheme-number">4</span></div>

  <svg class="bottle" viewBox="0 0 170 765" role="img" aria-label="Clear claret bottle with purple screwcap showing the label applied">
    <defs>
      <linearGradient id="glass" x1="0" x2="1">
        <stop offset="0" stop-color="#d9cdbd"/>
        <stop offset="0.5" stop-color="#f3ece2"/>
        <stop offset="1" stop-color="#cfc2b1"/>
      </linearGradient>
    </defs>
    <path d="M60 60 L110 60 L112 150 C114 200 165 220 165 280 L165 750 Q165 762 150 762 L20 762 Q5 762 5 750 L5 280 C5 220 56 200 58 150 Z" fill="url(#glass)"/>
    <rect x="55" y="4" width="60" height="110" rx="4" fill="var(--cap-purple)"/>
  </svg>

  <div class="bottle-label">
    <div class="mini-mark"><span class="dot"></span>Red Mo's</div>
    <div class="mini-wordmark">RED Mo's</div>
    <div class="mini-variety">PIGNOT GRIS <span>2012</span></div>
    <div class="mini-pattern" aria-hidden="true">Red Mo's</div>
    <div class="mini-volume">12% Vol.<br>750ml</div>
  </div>

  <div class="section-bar pms-bar">PMS Values</div>
  <ul class="swatches">
    <li><span class="chip chip-purple"></span>Inkline 7435</li>
    <li><span class="chip chip-black"></span>Inkline Black</li>
  </ul>
</main>
</body>
</html>
```